Brivora Distance Learning Website

Brivora provide e-learning and mixed learning solutions for individuals, colleges, organisations and B2B.
We need a modern, light and flat website design for Brivora. We want to to see the designer incorporate user experience(UX) design elements into the AI or PSD mockups. We would like to see designs that use pastel colors that compliment yellow and black of our logo.
We want our E-learning experience to accelerate learning and for the interface to be user friendly and intuitive. We want the designs to focus on quick access to course information, course reviews, learning progress and study advice. Quick and intuitive access to all content for our clients is one of our top priorities.
We would like designs for the following project 3 pages:
1. Learner homepage dashboard (see attached screenshot).
On this page the Learners need to:
- Login
- Have quick access to Packages and Courses.
- See other recommended courses (Below Packages and Courses)
- Possibly a left hand side column/menu with thumbnail icons (See lumeqa learner dashboard screenshot)
2. Homepage
See current sample
http://www.brivora-learn.example
We would like the designer to focus on creating a customized banner to enhance the home page.
3. Primary Landing/Marketing page
This page is geared towards customer acquisition with the focal point being the top banner (video or HD image).
And Course Preview content below.
See reference
http://brivora-learn.example/subscriptionPlans/marketing/MTc%3D/Mjc4Nw%3D%3D/Speaking%20Nepali%20%2B%20Nepali%20Snacks%20Bundle%20by%20Lorne%20Pike%20Vell
Other site we like:
- https://www.skillorva.example (We like the home page and top bar on courses page)
- http://www.tutorcrest.example
- http://pixelgrovelab.example (think this site looks great, love the lower graphics on the homepage)
Updates
Hello,
Thank you for taking the time to contribute to this web design competition. We would just like to point out a few things:
1. Please try to make the color palette similar to the colors used in the screenshot that we just uploaded ('possible color palette).
2. Please make the designs specific to each page: THE LEARNER HOMEPAGE, HOME PAGE, and the MARKETING LANDING PAGE.
We are very happy with the high quality of designs so far,
Cheers,
Ned Ru
VK-Studio
Also,
Please avoid using dark/bold elements in the designs. The ONLY elements that we want to be dark are the logo and the footer.
Any questions please ask,
Cheers,
Ned Ru
Vk-Studio
Hello,
Based on the round of feedback we just gave it would be great if you could complete further design changes by tomorrow, as we are pushed for time.
Thank you,
Ned Ru
VK-Studio

```html
<!DOCTYPE html>
<html lang="en">
<head>
<meta charset="utf-8">
<title>Brivora for Organisations and Academic Institutes</title>
<link rel="stylesheet" href="https://fonts.googleapis.com/css2?family=Raleway:wght@400;500;600;700&family=Arimo:wght@400;700&display=swap">
<style>
:root{
  --yellow:#f7bb23;
  --ink:#222;
  --text:#333;
  --muted:#666;
  --panel:#ebebeb;
  --card:#f5f5f5;
  --footer:#333;
  --btn-top:#8a8a8a;
  --btn-bot:#5e5e5e;
  --orange:#f0a81c;
  --rule:#999;
}
*{box-sizing:border-box;margin:0;padding:0}
html,body{width:1000px;height:1200px;overflow:hidden}
body{font-family:"Arimo",Arial,sans-serif;color:var(--text);background:var(--panel);position:relative}
.site-header{position:absolute;left:0;top:0;width:1000px;height:77px;background:#fff;box-shadow:0 1px 3px rgba(0,0,0,.12);z-index:2}
.brand{position:absolute;left:87px;top:18px;display:flex;align-items:center;gap:8px;font-family:"Raleway",sans-serif;font-weight:600;font-size:32px;color:var(--ink)}
.brand-dot{width:30px;height:30px;border-radius:50%;background:var(--yellow)}
.lang-btn{position:absolute;left:718px;top:25px;width:88px;height:26px;background:var(--yellow);border-radius:3px;font-size:13px;color:var(--ink);display:flex;align-items:center;justify-content:center}
.signin-btn{position:absolute;left:831px;top:25px;width:73px;height:26px;background:linear-gradient(var(--btn-top),var(--btn-bot));border-radius:3px;font-size:13px;color:#fff;display:flex;align-items:center;justify-content:center}
.hero{position:absolute;left:0;top:77px;width:1000px;height:478px}
.hero-photo{position:absolute;inset:0;background:radial-gradient(ellipse at 70% 35%,#f6dca0 0%,#efc36a 45%,#e3a94a 100%)}
.hero-title{position:absolute;left:0;top:112px;width:1000px;text-align:center;font-family:"Raleway",sans-serif;font-weight:700;font-size:42px;line-height:53px;color:#2b2b2b}
.search-panel{position:absolute;left:178px;top:249px;width:628px;height:124px;background:rgba(70,62,50,.85);border-radius:3px}
.search-panel h2{position:absolute;left:21px;top:20px;font-weight:400;font-size:22px;color:#fff}
.search-field{position:absolute;left:20px;top:62px;width:526px;height:38px;background:#fff;border-radius:3px 0 0 3px}
.search-submit{position:absolute;left:546px;top:62px;width:50px;height:38px;background:var(--yellow);border-radius:0 3px 3px 0;display:flex;align-items:center;justify-content:center}
.beta-tab{position:absolute;left:954px;top:220px;width:46px;height:137px;background:#8b8b8b;border-radius:4px 0 0 4px;border:1px solid #777}
.beta-tab span{position:absolute;left:50%;top:50%;transform:translate(-50%,-50%) rotate(-90deg);white-space:nowrap;color:#fff;font-family:"Raleway",sans-serif;font-size:19px}
.section-title{position:absolute;left:83px;top:582px;width:834px;height:44px;display:flex;align-items:center;gap:4px;font-family:"Raleway",sans-serif;font-weight:500;font-size:33px;line-height:44px;color:#444;white-space:nowrap}
.section-title::before,.section-title::after{content:"";flex:1;height:1px;background:var(--rule)}
.categories{position:absolute;left:83px;top:667px;width:197px;height:408px;background:#fff;box-shadow:0 1px 2px rgba(0,0,0,.15)}
.categories h3{height:42px;background:var(--yellow);font-family:"Raleway",sans-serif;font-weight:500;font-size:21px;color:var(--ink);padding:8px 12px}
.categories ul{list-style:none;padding-top:5px}
.categories li{height:35px;border-bottom:1px solid #e4e4e4;font-size:12px;color:var(--ink);padding:9px 0 0 21px;position:relative}
.categories li::before{content:"";position:absolute;left:12px;top:15px;width:3px;height:3px;background:#555}
.categories li:last-child{border-bottom:0}
.course-card{position:absolute;top:667px;width:185px;height:336px;background:#fff;border:1px solid #d4d4d4;border-radius:3px;box-shadow:0 1px 2px rgba(0,0,0,.1)}
.course-cover{position:absolute;left:9px;top:9px;width:165px;height:142px;background:var(--yellow);display:flex;flex-direction:column;align-items:center;justify-content:flex-end;padding-bottom:14px}
.course-cover b{font-family:"Raleway",sans-serif;font-size:20px;color:#fff;letter-spacing:1px}
.course-stats{position:absolute;left:0;top:159px;width:183px;height:37px;border-top:1px solid #ccc;border-bottom:1px solid #ccc;background:var(--card);display:flex}
.stat-cat{width:89px;border-right:1px solid #ccc;font-size:11px;padding:7px 0 0 17px;line-height:13px}
.stat-views{flex:1;text-align:center;font-size:12px;font-weight:700;padding-top:3px}
.course-body{position:absolute;left:0;top:196px;width:183px;height:138px;background:var(--card)}
.reviews{text-align:center;font-size:11px;padding-top:6px}
.stars{display:flex;justify-content:center;gap:2px;margin-top:3px}
.course-name{font-size:11px;line-height:13px;padding:11px 14px 0 14px;color:var(--ink)}
.course-author{font-size:10px;padding:2px 14px 0;color:var(--ink)}
.course-author small{font-size:8.5px;color:var(--muted)}
.details-btn{position:absolute;left:12px;top:295px;width:157px;height:28px;background:linear-gradient(var(--btn-top),var(--btn-bot));border-radius:3px;color:#fff;font-size:10.5px;font-weight:700;display:flex;align-items:center;justify-content:center;gap:6px}
.org-note{position:absolute;left:308px;top:1023px;width:608px}
.org-note h4{font-family:"Raleway",sans-serif;font-weight:500;font-size:15.5px;color:var(--orange)}
.org-note p{font-size:11.5px;line-height:17px;margin-top:5px;color:var(--ink)}
.site-footer{position:absolute;left:0;top:1117px;width:1000px;height:83px;background:var(--footer)}
.footer-links{position:absolute;left:91px;top:14px;list-style:none;font-size:11.5px;color:#ddd;line-height:18.5px}
.footer-brand{position:absolute;left:746px;top:18px;display:flex;align-items:center;gap:8px;font-family:"Raleway",sans-serif;font-weight:600;font-size:32px;color:#fff}
</style>
</head>
<body>
<header class="site-header">
  <div class="brand"><span class="brand-dot"></span>Brivora</div>
  <div class="lang-btn">English(US)</div>
  <div class="signin-btn">Sign In</div>
</header>

<section class="hero">
  <div class="hero-photo" role="img" aria-label="Warm yellow-toned photo of a learner working at a laptop"></div>
  <h1 class="hero-title">Brivora for Organisations and<br>Academic Institutes</h1>
  <div class="search-panel">
    <h2>What Can We Help You Learn Today?</h2>
    <div class="search-field"></div>
    <div class="search-submit">
      <svg width="26" height="26" viewBox="0 0 26 26"><circle cx="11" cy="11" r="8" fill="none" stroke="#111" stroke-width="3"/><line x1="17" y1="17" x2="23" y2="23" stroke="#111" stroke-width="3.5" stroke-linecap="round"/></svg>
    </div>
  </div>
  <div class="beta-tab"><span>Join Beta</span></div>
</section>

<h2 class="section-title">Learning Packages</h2>

<aside class="categories">
  <h3>Categories</h3>
  <ul>
    <li>Business and Finance</li>
    <li>Marketing</li>
    <li>IT &amp; Software</li>
    <li>Lifestyle</li>
    <li>Personal Development</li>
    <li>Photography</li>
    <li>Health and Fitness</li>
    <li>Education and Teaching</li>
    <li>Music</li>
    <li>Hotels and Hospitality</li>
  </ul>
</aside>

<article class="course-card" style="left:308px">
  <div class="course-cover" role="img" aria-label="Course cover artwork for Nepali Snacks"><b>Nepali Snacks</b></div>
  <div class="course-stats"><div class="stat-cat">Language<br>and...</div><div class="stat-views"><svg width="14" height="9" viewBox="0 0 14 9"><ellipse cx="7" cy="4.5" rx="6" ry="3.5" fill="none" stroke="#555" stroke-width="1.3"/><circle cx="7" cy="4.5" r="1.6" fill="#555"/></svg><br>Views 1417</div></div>
  <div class="course-body">
    <div class="reviews">Reviews</div>
    <div class="stars">
      <svg width="12" height="12" viewBox="0 0 12 12"><polygon points="6,0.5 7.6,4.2 11.5,4.5 8.5,7.1 9.4,11 6,8.9 2.6,11 3.5,7.1 0.5,4.5 4.4,4.2" fill="#f5b60f"/></svg>
      <svg width="12" height="12" viewBox="0 0 12 12"><polygon points="6,0.5 7.6,4.2 11.5,4.5 8.5,7.1 9.4,11 6,8.9 2.6,11 3.5,7.1 0.5,4.5 4.4,4.2" fill="#f5b60f"/></svg>
      <svg width="12" height="12" viewBox="0 0 12 12"><polygon points="6,0.5 7.6,4.2 11.5,4.5 8.5,7.1 9.4,11 6,8.9 2.6,11 3.5,7.1 0.5,4.5 4.4,4.2" fill="#f5b60f"/></svg>
      <svg width="12" height="12" viewBox="0 0 12 12"><polygon points="6,0.5 7.6,4.2 11.5,4.5 8.5,7.1 9.4,11 6,8.9 2.6,11 3.5,7.1 0.5,4.5 4.4,4.2" fill="#f5b60f"/></svg>
      <svg width="12" height="12" viewBox="0 0 12 12"><polygon points="6,0.5 7.6,4.2 11.5,4.5 8.5,7.1 9.4,11 6,8.9 2.6,11 3.5,7.1 0.5,4.5 4.4,4.2" fill="#999"/></svg>
    </div>
    <p class="course-name">Speaking Nepali Fundamentals Suite by Lorne Pike Vell</p>
    <p class="course-author">by <small>Lorne Vell</small></p>
  </div>
  <div class="details-btn"><svg width="22" height="8" viewBox="0 0 22 8"><rect x="0" y="0" width="7" height="8" fill="#fff"/><rect x="9" y="0" width="13" height="1.6" fill="#fff"/><rect x="9" y="3.2" width="13" height="1.6" fill="#fff"/><rect x="9" y="6.4" width="13" height="1.6" fill="#fff"/></svg>DETAILS</div>
</article>

<article class="course-card" style="left:519px">
  <div class="course-cover" role="img" aria-label="Course cover artwork for Nepali Snacks"><b>Nepali Snacks</b></div>
  <div class="course-stats"><div class="stat-cat">Language<br>and...</div><div class="stat-views"><svg width="14" height="9" viewBox="0 0 14 9"><ellipse cx="7" cy="4.5" rx="6" ry="3.5" fill="none" stroke="#555" stroke-width="1.3"/><circle cx="7" cy="4.5" r="1.6" fill="#555"/></svg><br>Views 1417</div></div>
  <div class="course-body">
    <div class="reviews">Reviews</div>
    <div class="stars">
      <svg width="12" height="12" viewBox="0 0 12 12"><polygon points="6,0.5 7.6,4.2 11.5,4.5 8.5,7.1 9.4,11 6,8.9 2.6,11 3.5,7.1 0.5,4.5 4.4,4.2" fill="#f5b60f"/></svg>
      <svg width="12" height="12" viewBox="0 0 12 12"><polygon points="6,0.5 7.6,4.2 11.5,4.5 8.5,7.1 9.4,11 6,8.9 2.6,11 3.5,7.1 0.5,4.5 4.4,4.2" fill="#f5b60f"/></svg>
      <svg width="12" height="12" viewBox="0 0 12 12"><polygon points="6,0.5 7.6,4.2 11.5,4.5 8.5,7.1 9.4,11 6,8.9 2.6,11 3.5,7.1 0.5,4.5 4.4,4.2" fill="#f5b60f"/></svg>
      <svg width="12" height="12" viewBox="0 0 12 12"><polygon points="6,0.5 7.6,4.2 11.5,4.5 8.5,7.1 9.4,11 6,8.9 2.6,11 3.5,7.1 0.5,4.5 4.4,4.2" fill="#f5b60f"/></svg>
      <svg width="12" height="12" viewBox="0 0 12 12"><polygon points="6,0.5 7.6,4.2 11.5,4.5 8.5,7.1 9.4,11 6,8.9 2.6,11 3.5,7.1 0.5,4.5 4.4,4.2" fill="#999"/></svg>
    </div>
    <p class="course-name">Speaking Nepali Fundamentals Suite by Lorne Pike Vell</p>
    <p class="course-author">by <small>Lorne Vell</small></p>
  </div>
  <div class="details-btn"><svg width="22" height="8" viewBox="0 0 22 8"><rect x="0" y="0" width="7" height="8" fill="#fff"/><rect x="9" y="0" width="13" height="1.6" fill="#fff"/><rect x="9" y="3.2" width="13" height="1.6" fill="#fff"/><rect x="9" y="6.4" width="13" height="1.6" fill="#fff"/></svg>DETAILS</div>
</article>

<article class="course-card" style="left:731px">
  <div class="course-cover" role="img" aria-label="Course cover artwork for Nepali Snacks"><b>Nepali Snacks</b></div>
  <div class="course-stats"><div class="stat-cat">Language<br>and...</div><div class="stat-views"><svg width="14" height="9" viewBox="0 0 14 9"><ellipse cx="7" cy="4.5" rx="6" ry="3.5" fill="none" stroke="#555" stroke-width="1.3"/><circle cx="7" cy="4.5" r="1.6" fill="#555"/></svg><br>Views 1417</div></div>
  <div class="course-body">
    <div class="reviews">Reviews</div>
    <div class="stars">
      <svg width="12" height="12" viewBox="0 0 12 12"><polygon points="6,0.5 7.6,4.2 11.5,4.5 8.5,7.1 9.4,11 6,8.9 2.6,11 3.5,7.1 0.5,4.5 4.4,4.2" fill="#f5b60f"/></svg>
      <svg width="12" height="12" viewBox="0 0 12 12"><polygon points="6,0.5 7.6,4.2 11.5,4.5 8.5,7.1 9.4,11 6,8.9 2.6,11 3.5,7.1 0.5,4.5 4.4,4.2" fill="#f5b60f"/></svg>
      <svg width="12" height="12" viewBox="0 0 12 12"><polygon points="6,0.5 7.6,4.2 11.5,4.5 8.5,7.1 9.4,11 6,8.9 2.6,11 3.5,7.1 0.5,4.5 4.4,4.2" fill="#f5b60f"/></svg>
      <svg width="12" height="12" viewBox="0 0 12 12"><polygon points="6,0.5 7.6,4.2 11.5,4.5 8.5,7.1 9.4,11 6,8.9 2.6,11 3.5,7.1 0.5,4.5 4.4,4.2" fill="#f5b60f"/></svg>
      <svg width="12" height="12" viewBox="0 0 12 12"><polygon points="6,0.5 7.6,4.2 11.5,4.5 8.5,7.1 9.4,11 6,8.9 2.6,11 3.5,7.1 0.5,4.5 4.4,4.2" fill="#999"/></svg>
    </div>
    <p class="course-name">Speaking Nepali Fundamentals Suite by Lorne Pike Vell</p>
    <p class="course-author">by <small>Lorne Vell</small></p>
  </div>
  <div class="details-btn"><svg width="22" height="8" viewBox="0 0 22 8"><rect x="0" y="0" width="7" height="8" fill="#fff"/><rect x="9" y="0" width="13" height="1.6" fill="#fff"/><rect x="9" y="3.2" width="13" height="1.6" fill="#fff"/><rect x="9" y="6.4" width="13" height="1.6" fill="#fff"/></svg>DETAILS</div>
</article>

<section class="org-note">
  <h4>Learning for Organisations and Educational Institutions.</h4>
  <p>Launching Soon! - Brivora will be launching services to integrate Brivora's learning platform into Organisations and Learning Institutes to support Online, Interactive and Blended Learning.</p>
</section>

<footer class="site-footer">
  <ul class="footer-links">
    <li>Copyright © 2015 Brivora.com</li>
    <li>Terms of Use</li>
    <li>Privacy Policy</li>
  </ul>
  <div class="footer-brand"><span class="brand-dot"></span>Brivora</div>
</footer>
</body>
</html>
```